A website where experts collaborate on your project

I am building a new website where experts (yes, like designers) collaborate on projects with the project owner. More minds = more collaboration = better end product. Please see Pelmora(dot)com for a quick landing page I created for collaborating on presentations (although there will be many project types offered)

I am looking for a DESIGNER LONG TERM, but for now, just need initial mock ups to show the web programmers.

I have 21 Word documents loosely designed, what I would like to see here is a theme. Please DO NOT GO OFF WHAT YOU CURRENTLY SEE AT PELMORA. What is up now is only a quick landing page.

You can view a Word doc of the homepage here:
https://www.filevanta.com/s/qx83kdm2/home.docx?dl=0

WHAT AM I LOOKING FOR?
A clean, well designed theme.

Here is a link to the logo:
https://www.filevanta.com/s/mr47tpz9/logo%20-%20horizontal.tif?dl=0
-----------------------------------------
Here are a few sites I like the design of and what I like about them:
www.quenbrook.com-all around my favorite, beautiful graphics, clean layout, bold use of colors on a dark background
Ravelto.com- clean layout, The use of humans and bubble style elements.
Mintharbor.com :) clean, bold, unique pop art style but professional
plumevault.com - From the unique colors and artwork and the ability of that art to not interfere with the important elements of the site
sparkwidgets.com-clean, nice colors, well organized and separated sections.
www.dunmereco.com-love the font, use of colors and sectionalized style

All in all, I am not picky and open to so many styles. I would ultimately like the designer I pick to design all 21 pages.
Updates

Hello everyone,Moving forward, I would like you all to pay special attention to the section in my brief titled "Here are a few sites I like the design of and what I like about them". Please see below, I handpicked each one of these as sites I really like. Thank you.Here are a few sites I like the design of and what I like about them:Ravelto.com- clean layout, The use of humans and bubble style elements.Mintharbor.com :) clean, bold, unique pop art style but professionalwriteraccess.com - From the unique colors and artwork and the ability of that art to not interfere with the important elements of the sitegrowthgeeks.com-clean, nice colors, well organized and separated sections.www.dunmereco.com-love the font, use of colors and sectionalized stylewww.quenbrook.com-beautiful graphics, clean layout, bold use of colors----------------------------------------- Added Tuesday, November 24, 2015

I updated the homepage, you can see it here:https://www.dropbox.com/s/kwlkbsookq3cg2m/1new%20homepage.docx?dl=0I am modeling it after my favorite designed site: triplelift.comI love the dark colors with the orange glowing style boldness of the buttons. It's real clean too. Added Tuesday, November 24, 2015

Target Market(s)

small business owners, marketers, freelancer writers, graphic designers,

Industry/Entity Type

Building

Number of Pages Required

5+ page

Requirements
Must have
• I can't think of anything the project must have.
Nice to have
• WHAT AM I LOOKING FOR?
• A clean, well designed theme. I had a designer do a bit of work putting elements together, I found it to be very plain, but I like the Application Page (https://www.filevanta.com/s/jb19ckr3/Pelmora-Website.ai?dl=0)
• Here is a link to the logo:
• https://www.filevanta.com/s/mr47tpz9/logo%20-%20horizontal.tif?dl=0
• Here are a few sites I like the design of and what I like about them:
• Ravelto.com- clean layout, The use of humans and bubble style elements.
• Mintharbor.com :) clean, bold, unique pop art style but professional
• plumevault.com - From the unique colors and artwork and the ability of that art to not interfere with the important elements of the site
• sparkwidgets.com-clean, nice colors, well organized and separated sections.
• www.dunmereco.com-love the font, use of colors and sectionalized style
• www.quenbrook.com-beautiful graphics, clean layout, bold use of colors
• -----------------------------------------
Should not have
• out of the boxed, templated style website. I want this site to be memorable and not look like a thousand others

```html
<!DOCTYPE html>
<html lang="en">
<head>
<meta charset="utf-8">
<title>Pelmora – Experts collaborating on your project</title>
<link rel="stylesheet" href="https://fonts.googleapis.com/css2?family=Open+Sans:wght@400;600;700&family=Roboto:wght@400;500;700&display=swap">
<style>
:root{
  --teal:#4fb0cd;
  --teal-dark:#3d8fa8;
  --orange:#f7941d;
  --ink:#333333;
  --muted:#666666;
  --card:#f2f2f2;
  --rule:#e3e3e3;
  --badge:#b9b9b9;
  --footer:#5bb3cc;
  --white:#ffffff;
}
*{box-sizing:border-box;margin:0;padding:0}
html,body{width:1200px;height:2635px;overflow:hidden;background:var(--white)}
body{position:relative;font-family:"Roboto",sans-serif;color:var(--ink)}
ul{list-style:none}
.abs{position:absolute}

/* header */
.site-header{left:0;top:0;width:1200px;height:130px}
.brand{left:152px;top:40px;display:flex;align-items:center;gap:14px}
.brand-name{font-family:"Open Sans",sans-serif;font-weight:700;font-size:32px;color:var(--orange);letter-spacing:-.5px}
.brand-dot{width:40px;height:40px;border-radius:50%;background:var(--orange)}
.search{left:562px;top:23px;display:flex;height:39px}
.search-select{width:173px;border:1px solid #cfcfcf;font-size:14px;color:var(--muted);padding:10px 12px;position:relative;background:#fff}
.search-select::after{content:"";position:absolute;right:12px;top:16px;border:6px solid transparent;border-top-color:#888}
.search-btn{width:85px;background:var(--orange);color:#fff;font-weight:700;font-size:14px;display:flex;align-items:center;justify-content:center}
.notify{left:933px;top:30px;font-size:13px;color:var(--muted);display:flex;align-items:center;gap:8px}
.notify-badge{width:34px;height:34px;border:2px solid var(--orange);border-radius:50%;display:flex;align-items:center;justify-content:center}
.notify-badge span{width:24px;height:24px;border-radius:50%;background:var(--orange);color:#fff;font-size:12px;font-weight:700;display:flex;align-items:center;justify-content:center}
.main-nav{left:562px;top:88px;display:flex;gap:0;font-size:15px}
.main-nav a{color:var(--ink);text-decoration:none;padding:5px 12px;margin-right:30px}
.main-nav a.active{background:var(--orange);color:#fff;padding:5px 15px}

/* hero */
.hero{left:0;top:130px;width:1200px;height:500px;background:linear-gradient(160deg,#6d7f86 0%,#3d4d57 45%,#5a5047 75%,#8a7766 100%)}
.hero-copy{left:0;top:292px;width:1200px;text-align:center;color:#fff}
.hero-title{font-family:"Open Sans",sans-serif;font-weight:700;font-size:30px;letter-spacing:.5px}
.hero-sub{font-size:19px;margin-top:6px}
.hero-btn{display:inline-flex;align-items:center;justify-content:center;gap:10px;margin-top:24px;width:222px;height:47px;background:var(--teal);color:#fff;font-family:"Open Sans",sans-serif;font-weight:700;font-size:17px;letter-spacing:2px}
.hero-dots{left:0;top:593px;width:1200px;display:flex;justify-content:center;gap:31px}
.hero-dots i{width:12px;height:12px;border-radius:50%;background:#fff}
.hero-dots i.on{background:var(--orange)}

/* sidebar */
.sidebar{left:153px;top:664px;width:230px}
.filters-title{font-size:17px;color:var(--teal);padding-bottom:8px;border-bottom:2px solid var(--teal);margin-bottom:18px}
.filter-block{padding-bottom:18px;margin-bottom:20px;border-bottom:4px solid var(--rule)}
.filter-head{font-size:15px;display:flex;align-items:center;gap:8px;margin-bottom:12px}
.filter-head svg{width:14px;height:14px}
.filter-list li{font-size:13px;color:var(--muted);line-height:24px}
.slider{position:relative;height:20px;margin:6px 0 4px}
.slider .track{position:absolute;left:0;right:0;top:8px;height:4px;background:#d5e9f0}
.slider .fill{position:absolute;left:6px;width:140px;top:8px;height:4px;background:var(--teal)}
.slider .knob{position:absolute;top:1px;width:18px;height:18px;border-radius:50%;background:#bfe1ec;border:2px solid var(--teal)}
.price-range{display:flex;justify-content:space-between;font-size:12px;color:var(--muted)}
.time-btns{display:flex;justify-content:space-between}
.time-btns span{width:106px;height:30px;display:flex;align-items:center;justify-content:center;font-size:13px;color:#fff}
.btn-teal{background:var(--teal)}
.btn-orange{background:var(--orange)}
.tags{font-size:13px;color:var(--muted);line-height:24px}
.save-btn{height:40px;background:var(--orange);color:#fff;font-family:"Open Sans",sans-serif;font-weight:700;font-size:18px;letter-spacing:3px;display:flex;align-items:center;justify-content:center}

/* offer */
.offer{left:418px;top:668px;width:629px;height:105px;background:var(--teal);color:#fff;padding:18px 28px;display:flex;justify-content:space-between}
.offer-text{font-size:21px;line-height:30px}
.offer-text b{font-size:27px}
.timer-title{font-size:16px;font-weight:700;margin-bottom:6px}
.timer{display:flex;gap:10px}
.timer-unit{text-align:center;font-size:10px}
.timer-digits{display:flex;gap:3px;margin-top:2px}
.timer-digits span{width:17px;height:22px;background:#fff;color:var(--ink);font-size:14px;font-weight:700;display:flex;align-items:center;justify-content:center}

/* section headings */
.section-title{font-size:24px;color:var(--teal);font-weight:400}
.sort{left:668px;top:802px;display:flex;align-items:center;gap:14px;font-size:12px;color:var(--muted)}
.sort-select{height:28px;border:1px solid #cfcfcf;padding:6px 10px;position:relative;font-size:11px}
.sort-select::after{content:"";position:absolute;right:8px;top:11px;border:5px solid transparent;border-top-color:#888}

/* project cards */
.grid{display:grid;grid-template-columns:308px 307px;column-gap:14px;row-gap:14px}
.card{position:relative;background:var(--card);height:192px;padding:18px 18px 0 98px}
.avatar{position:absolute;left:16px;top:22px;width:50px;height:50px;border-radius:50%;background:linear-gradient(135deg,#c9c2b8,#7d8a92);box-shadow:4px 5px 0 0 var(--orange)}
.card p{font-size:13px;line-height:21px;color:var(--muted);text-align:justify;height:84px}
.price{font-size:21px;font-weight:700;color:var(--orange);margin-top:17px}
.badge{position:absolute;right:16px;bottom:16px;background:var(--badge);color:#fff;font-size:10px;padding:3px 8px;border-radius:2px}

/* testimonials */
.testi-head{left:153px;top:2160px;width:894px;display:flex;justify-content:space-between;align-items:center}
.arrows{display:flex;gap:4px}
.arrows span{width:18px;height:18px;border-radius:50%;background:#9a9a9a}
.testi{left:153px;top:2203px;width:894px;height:167px;border:1px solid var(--rule);display:grid;grid-template-columns:1fr 1fr}
.quote{padding:22px 22px 0 22px;position:relative}
.quote+.quote{border-left:1px solid var(--rule)}
.quote-person{display:flex;align-items:center;gap:18px;margin-bottom:28px}
.quote-person .avatar{position:static;width:46px;height:46px}
.quote-meta{border-left:1px solid #ccc;padding-left:14px}
.quote-name{font-size:13px;color:var(--teal)}
.quote-role{font-size:11px;color:var(--muted);margin-top:4px}
.quote-text{font-size:13px;line-height:21px;color:var(--muted);padding-left:50px;position:relative}
.quote-text::before{content:"\201C";position:absolute;left:22px;top:-6px;font-size:30px;color:#ccc;font-family:"Open Sans",sans-serif}

/* footer */
.site-footer{left:0;top:2404px;width:1200px;height:231px;background:var(--footer);color:#fff;text-align:center}
.follow{padding-top:33px;font-family:"Open Sans",sans-serif;font-weight:700;font-size:13px;letter-spacing:2px}
.socials{display:flex;justify-content:center;gap:8px;margin-top:16px}
.socials i{width:31px;height:31px;border-radius:50%;background:#4a7fb0}
.socials i:nth-child(2){background:#2aa3e0}
.socials i:nth-child(3){background:#f26b21}
.socials i:nth-child(4){background:#3a6a9e}
.socials i:nth-child(5){background:#e23b2c}
.footer-nav{margin:26px auto 0;width:500px;padding-bottom:14px;border-bottom:1px solid rgba(255,255,255,.4);font-family:"Open Sans",sans-serif;font-weight:700;font-size:13px;letter-spacing:2px}
.footer-nav span{margin:0 6px}
.copyright{font-size:12px;margin-top:16px}
</style>
</head>
<body>

<header class="site-header abs">
  <div class="brand abs"><span class="brand-name">Pelmora</span><span class="brand-dot"></span></div>
  <div class="search abs"><div class="search-select">Freelancers</div><div class="search-btn">SEARCH</div></div>
  <div class="notify abs">Notification <span class="notify-badge"><span>4</span></span></div>
  <nav class="main-nav abs">
    <a class="active">Home</a><a>Projects</a><a>How it Works</a><a>Plans</a><a>My Account</a>
  </nav>
</header>

<section class="hero abs" role="img" aria-label="Photo of a smiling group of five young professionals in an office"></section>
<div class="hero-copy abs">
  <h1 class="hero-title">CONVERT MORE CUSTOMERS</h1>
  <p class="hero-sub">Experience the power of experts collaborating on your project.</p>
  <div class="hero-btn">GET STARTED <svg width="14" height="12" viewBox="0 0 14 12"><path d="M1 1l5 5-5 5M7 1l5 5-5 5" fill="none" stroke="#fff" stroke-width="2"/></svg></div>
</div>
<div class="hero-dots abs"><i></i><i></i><i class="on"></i><i></i><i></i><i></i></div>

<aside class="sidebar abs">
  <h2 class="filters-title">Filters</h2>
  <div class="filter-block">
    <div class="filter-head">$ &nbsp;Price</div>
    <div class="slider"><div class="track"></div><div class="fill"></div><div class="knob" style="left:0"></div><div class="knob" style="left:135px"></div></div>
    <div class="price-range"><span>$20</span><span>$1,000+</span></div>
  </div>
  <div class="filter-block">
    <div class="filter-head"><svg viewBox="0 0 14 14"><circle cx="7" cy="7" r="6.5" fill="#333"/></svg>Country</div>
    <ul class="filter-list"><li>Australia</li><li>England</li><li>India</li><li>South Africa</li><li>United States</li><li>Spain</li><li>France</li><li>Canada</li></ul>
  </div>
  <div class="filter-block">
    <div class="filter-head"><svg viewBox="0 0 14 14"><rect x="1" y="2" width="10" height="11" fill="none" stroke="#333" stroke-width="1.5"/><path d="M6 9l7-7" stroke="#333" stroke-width="2"/></svg>Categories</div>
    <ul class="filter-list"><li>All Categories</li><li>Inbound Content</li><li>Social Media</li><li>Lead Generation</li><li>Public Relations</li><li>Conversion Rates</li><li>Virality</li><li>Email Marketing</li><li>Copywriting</li><li>Paid Traffic</li><li>Analytics</li><li>Mobile Apps</li><li>SEO</li><li>Sales</li><li>Development</li><li>Design</li></ul>
  </div>
  <div class="filter-block">
    <div class="filter-head"><svg viewBox="0 0 14 14"><circle cx="7" cy="7" r="6" fill="none" stroke="#333" stroke-width="1.5"/><path d="M7 3v4h3" fill="none" stroke="#333" stroke-width="1.5"/></svg>Time Left</div>
    <div class="time-btns"><span class="btn-teal">Time Left</span><span class="btn-orange">Experied</span></div>
  </div>
  <div class="filter-block">
    <div class="filter-head"><svg viewBox="0 0 14 14"><path d="M2 1h7l3 3v9H2z" fill="#333"/></svg>Contains adult content</div>
    <ul class="filter-list"><li>Analytics</li><li>Mobile Apps</li><li>SEO</li><li>Sales</li><li>Development</li><li>Design</li></ul>
  </div>
  <div class="filter-block">
    <div class="filter-head"><svg viewBox="0 0 14 14"><circle cx="4.5" cy="5" r="3" fill="none" stroke="#333" stroke-width="1.6"/><path d="M7 7l6 6M10 10l2-2" stroke="#333" stroke-width="1.6"/></svg>Keywords</div>
    <div class="tags">Analytics &nbsp;| &nbsp;Mobile Apps &nbsp;| &nbsp;SEO<br>Sales &nbsp;| &nbsp;Development &nbsp;| &nbsp;Design</div>
  </div>
  <div class="filter-block">
    <div class="filter-head"><svg viewBox="0 0 14 14"><circle cx="2.5" cy="11.5" r="1.8" fill="#333"/><path d="M1 6a7 7 0 0 1 7 7M1 1a12 12 0 0 1 12 12" fill="none" stroke="#333" stroke-width="1.8"/></svg>Followers</div>
  </div>
  <div class="save-btn">SAVE</div>
</aside>

<div class="offer abs">
  <div class="offer-text">Morbi in ante arcu.<br>Maecenas sit ametsemvel .<b>$80</b></div>
  <div>
    <div class="timer-title">Time Left</div>
    <div class="timer">
      <div class="timer-unit">Days<div class="timer-digits"><span>0</span><span>6</span></div></div>
      <div class="timer-unit">Hours<div class="timer-digits"><span>1</span><span>8</span></div></div>
      <div class="timer-unit">Minutes<div class="timer-digits"><span>2</span><span>0</span></div></div>
      <div class="timer-unit">Seconds<div class="timer-digits"><span>3</span><span>0</span></div></div>
    </div>
  </div>
</div>

<h2 class="section-title abs" style="left:418px;top:800px">Crowd Projects</h2>
<div class="sort abs">Sort by :
  <span class="sort-select" style="width:90px">Price</span>
  <span class="sort-select" style="width:90px">Country</span>
  <span class="sort-select" style="width:98px">Time Left</span>
</div>

<div class="grid abs" style="left:418px;top:849px">
  <article class="card"><span class="avatar" role="img" aria-label="Expert portrait"></span><p>Lorem Ipsum is simply dummy text of the printing and typesetting industry. Lorem Ipsum has been.</p><div class="price">$ 80.00</div><span class="badge">🕓 U.K. Time Left : 2 Days</span></article>
  <article class="card"><span class="avatar" role="img" aria-label="Expert portrait"></span><p>It is a long established fact that a reader will be distracted by the readable content of a page when looking at its layout.</p><div class="price">$ 65.00</div><span class="badge">🕓 U.K. Time Left : 2 Days</span></article>
  <article class="card"><span class="avatar" role="img" aria-label="Expert portrait"></span><p>There are many variations of passages of Lorem Ipsum available, but the majority have suffered .</p><div class="price">$ 75.00</div><span class="badge">🕓 U.K. Time Left : 2 Days</span></article>
  <article class="card"><span class="avatar" role="img" aria-label="Expert portrait"></span><p>But I must explain to you how all this mistaken idea of denouncing pleasure and praising pain was.</p><div class="price">$ 91.00</div><span class="badge">🕓 U.K. Time Left : 2 Days</span></article>
</div>

<h2 class="section-title abs" style="left:418px;top:1274px">Featured Projects</h2>
<div class="grid abs" style="left:418px;top:1321px">
  <article class="card"><span class="avatar" role="img" aria-label="Expert portrait"></span><p>But I must explain to you how all this mistaken idea of denouncing pleasure and praising.</p><div class="price">$ 80.00</div><span class="badge">🕓 U.S. Time Left : 6 Days</span></article>
  <article class="card"><span class="avatar" role="img" aria-label="Expert portrait"></span><p>At vero eos et accusamus et iusto odio dignissimos ducimus qui blanditiis praesentium voluptatum.</p><div class="price">$ 65.00</div><span class="badge">🕓 U.S. Time Left : 2 Days</span></article>
  <article class="card"><span class="avatar" role="img" aria-label="Expert portrait"></span><p>On the other hand, we denounce with righteous indignation and dislike men who are so beguiled and demoralized.</p><div class="price">$ 250.00</div><span class="badge">🕓 U.S. Time Left : 2 Days</span></article>
  <article class="card"><span class="avatar" role="img" aria-label="Expert portrait"></span><p>These cases are perfectly simple and easy to distinguish. In a free hour, when our power of choice is untrammelled.</p><div class="price">$ 105.00</div><span class="badge">🕓 U.S. Time Left : 2 Days</span></article>
  <article class="card"><span class="avatar" role="img" aria-label="Expert portrait"></span><p>There are many variations of passages of Lorem Ipsum available, but the majority have suffered .</p><div class="price">$ 93.00</div><span class="badge">🕓 U.S Time Left : 2 Days</span></article>
  <article class="card"><span class="avatar" role="img" aria-label="Expert portrait"></span><p>But I must explain to you how all this mistaken idea of denouncing pleasure and praising pain was.</p><div class="price">$ 60.00</div><span class="badge">🕓 U.S. Time Left : 2 Days</span></article>
  <article class="card"><span class="avatar" role="img" aria-label="Expert portrait"></span><p>Temporibus autem quibusdam et aut officiis debitis aut rerum necessitatibus saepe eveniet ut et voluptates.</p><div class="price">$ 130.00</div><span class="badge">🕓 U.S. Time Left : 2 Days</span></article>
  <article class="card"><span class="avatar" role="img" aria-label="Expert portrait"></span><p>Combined with a handful of model sentence structures, to generate Lorem Ipsum which looks reasonable.</p><div class="price">$ 91.00</div><span class="badge">🕓 U.S. Time Left : 2 Days</span></article>
</div>

<div class="testi-head abs"><h2 class="section-title">Testimonials</h2><div class="arrows"><span></span><span></span></div></div>
<div class="testi abs">
  <div class="quote">
    <div class="quote-person"><span class="avatar" role="img" aria-label="Client portrait"></span><div class="quote-meta"><div class="quote-name">Dara Quill</div><div class="quote-role">CEO, Ledger Nine</div></div></div>
    <p class="quote-text">With Pelmora I have multiple experts perfecting my content and I only pay for the feedback I find valuable. It's perfect.</p>
  </div>
  <div class="quote">
    <div class="quote-person"><span class="avatar" role="img" aria-label="Client portrait"></span><div class="quote-meta"><div class="quote-name">Owen Marsh</div><div class="quote-role">CEO, Brightfold</div></div></div>
    <p class="quote-text">Before you put any content in front of your audience, crowdsource it with Pelmora, you won't regret it.</p>
  </div>
</div>

<footer class="site-footer abs">
  <div class="follow">FOLLOW US ON</div>
  <div class="socials"><i></i><i></i><i></i><i></i><i></i></div>
  <div class="footer-nav">HOME <span>\</span> PROJECTS <span>\</span> HOW IT WORKS <span>\</span> PLANS <span>\</span> MY ACCOUNT</div>
  <div class="copyright">Copyrights @ 2015 All Rights Reserved</div>
</footer>

</body>
</html>
```